Email Banner (LoomDigest)

We require an email banner for our email promotions sent to prospect clients. The banner needs to contain the wording LoomDigest and use the same colour scheme as the logos attached.

This is for B2B professional's so needs to look like a place you would come to read technology articles.

```html
<!DOCTYPE html>
<html lang="en">
<head>
<meta charset="utf-8">
<title>LoomDigest Email Banner</title>
<link rel="stylesheet" href="https://fonts.googleapis.com/css2?family=Montserrat:wght@600;700&display=swap">
<style>
  :root {
    --page-bg: #c9c9c9;
    --brand-blue: #0a6fc0;
    --brand-teal: #1f8f86;
    --brand-green: #4fa93b;
    --brand-lime: #5aac34;
    --ink-white: #ffffff;
    --ink-dark: #1c1c1c;
    --strip-navy: #0c1a38;
    --icon-green: #6cc04a;
  }
  * { margin: 0; padding: 0; box-sizing: border-box; }
  html, body {
    width: 1200px;
    height: 512px;
    overflow: hidden;
    background: var(--page-bg);
  }
  .banner {
    position: absolute;
    left: 74px;
    top: 124px;
    width: 1066px;
    height: 246px;
    overflow: hidden;
    background: linear-gradient(100deg, var(--brand-blue) 0%, var(--brand-teal) 30%, #2f9a5e 55%, var(--brand-green) 80%, var(--brand-lime) 100%);
    font-family: "Montserrat", sans-serif;
  }
  .brand-name {
    position: absolute;
    left: 46px;
    top: 39px;
    font-size: 84px;
    font-weight: 600;
    line-height: 1;
    letter-spacing: -1px;
    color: var(--ink-white);
    white-space: nowrap;
  }
  .contact-strip {
    position: absolute;
    left: 0;
    top: 171px;
    width: 1066px;
    height: 43px;
  }
  .strip-shapes { position: absolute; left: 0; top: 0; }
  .contact-phone,
  .contact-web {
    position: absolute;
    top: 0;
    height: 43px;
    display: flex;
    align-items: center;
    gap: 9px;
    font-weight: 700;
    line-height: 1;
    white-space: nowrap;
  }
  .contact-icon { flex: 0 0 auto; display: block; }
  .contact-phone {
    left: 75px;
    font-size: 28px;
    color: var(--ink-dark);
  }
  .contact-web {
    left: 356px;
    font-size: 23px;
    letter-spacing: 7px;
    color: var(--ink-white);
  }
</style>
</head>
<body>
  <div class="banner">
    <div class="brand-name">LoomDigest.io</div>

    <div class="contact-strip">
      <svg class="strip-shapes" width="1066" height="43" viewBox="0 0 1066 43" aria-hidden="true">
        <polygon points="30,43 57,0 352,0 315,43" fill="var(--ink-white)"/>
        <polygon points="315,43 352,0 790,0 748,43" fill="var(--strip-navy)"/>
      </svg>

      <div class="contact-phone">
        <svg class="contact-icon" width="22" height="22" viewBox="0 0 22 22" aria-hidden="true">
          <circle cx="11" cy="11" r="11" fill="var(--icon-green)"/>
          <path d="M7.2 5.5c.5-.4 1.1-.3 1.4.2l1 1.7c.3.5.2 1-.2 1.3l-.7.6c.6 1.4 1.6 2.5 3 3.1l.6-.7c.3-.4.9-.5 1.3-.2l1.7 1c.5.3.6.9.2 1.4l-.8.9c-.6.6-1.5.8-2.3.4-2.9-1.3-5-3.4-6.2-6.3-.3-.8-.1-1.6.5-2.2z" fill="var(--ink-white)"/>
        </svg>
        <span>555 0142 0199</span>
      </div>

      <div class="contact-web">
        <svg class="contact-icon" width="22" height="22" viewBox="0 0 22 22" aria-hidden="true" fill="none" stroke="var(--icon-green)" stroke-width="1.8">
          <circle cx="11" cy="11" r="9.5"/>
          <ellipse cx="11" cy="11" rx="4.2" ry="9.5"/>
          <line x1="1.5" y1="11" x2="20.5" y2="11"/>
          <line x1="3" y1="6.2" x2="19" y2="6.2"/>
          <line x1="3" y1="15.8" x2="19" y2="15.8"/>
        </svg>
        <span>www.loomdigest.io</span>
      </div>
    </div>
  </div>
</body>
</html>
```